Professional Service Business Branding Upgrade and Stationary

Brand to be KORvalley- KOR to be bold and different colour to the smaller font regional.
-colours to be the same or similar to Upper Coastal Plains AFL Football club
1.To include a style guide - Font is optional but must be reflective of professional service brand and image.
2.Logo attached but colours obviously change
Tag line - Thinking outside the box ( don't have to use this in new logo. Could do one with tag line and one without perhaps)
3.Word document including headings, tables and font standardised
4.Power Point
5.Note Pad - bottom of page to read - Business Transformation, Strategic Planning, Sales and Marketing, Export Grants.

Target Market(s)

Small to medium size regional businesses notably manufacturers and family businesses

```html
<!DOCTYPE html>
<html lang="en">
<head>
<meta charset="utf-8">
<title>KORvalley Note Pad</title>
<link href="https://fonts.googleapis.com/css2?family=Montserrat:wght@400;500;600;700&display=swap" rel="stylesheet">
<style>
  :root {
    --orange: #f39a4c;
    --charcoal: #4a4a4c;
    --grey-text: #6d6e71;
    --rule: #dcdcdc;
    --box-border: #c9c9c9;
    --label-bg: #f4f4f4;
    --paper: #ffffff;
  }
  * { margin: 0; padding: 0; box-sizing: border-box; }
  html, body { width: 880px; height: 1200px; overflow: hidden; background: var(--paper); }
  body { font-family: "Montserrat", Arial, sans-serif; position: relative; }

  .brand {
    position: absolute; left: 94px; top: 78px;
  }
  .brand-name {
    font-size: 34px; font-weight: 600; color: var(--charcoal);
    letter-spacing: 4px; line-height: 1; text-transform: uppercase;
  }

  .details {
    position: absolute; left: 543px; top: 46px; width: 276px;
    border-collapse: collapse;
  }
  .details th, .details td {
    border: 1px solid var(--box-border); height: 27px;
  }
  .details th {
    width: 94px; background: var(--label-bg); text-align: left;
    padding-left: 8px; font-size: 10px; font-weight: 600;
    letter-spacing: 1px; color: var(--charcoal);
  }

  .writing-area {
    position: absolute; left: 73px; top: 250px; width: 747px; height: 762px;
    background: repeating-linear-gradient(
      to bottom,
      var(--rule) 0, var(--rule) 1px,
      transparent 1px, transparent 18px
    );
  }

  .tagline {
    position: absolute; left: 0; right: 0; top: 1100px;
    text-align: center; font-size: 19px; font-weight: 500;
    letter-spacing: 6px; color: var(--charcoal);
  }
  .services {
    position: absolute; left: 0; right: 0; top: 1140px;
    text-align: center; font-size: 12px; color: var(--grey-text);
  }
  .services .sep { color: var(--orange); margin: 0 6px; }
</style>
</head>
<body>
  <header class="brand">
    <div class="brand-name">KORvalley</div>
  </header>

  <table class="details">
    <tr><th>NAME</th><td></td></tr>
    <tr><th>COMPANY</th><td></td></tr>
    <tr><th>DATE</th><td></td></tr>
  </table>

  <main class="writing-area"></main>

  <footer>
    <p class="tagline">THINKING OUTSIDE THE SQUARE</p>
    <p class="services">Business Transformation<span class="sep">•</span>Strategic Planning<span class="sep">•</span>Sales and Marketing<span class="sep">•</span>Export Grants</p>
  </footer>
</body>
</html>
```